Fern Lattice Table & Chair Rentals

We need a business card for a table and chair rental company. We rent tables and chairs for weddings, funerals, business events and parties. We want something that looks clean and elegant while not being too busy. We would like colors in the green and blue hues and avoiding anything orange. We want to make sure the font is large enough to be seen easily.

Target Market(s)

Wedding & Event Rentals

Industry/Entity Type

Events

Contact Information for Business Card

Fern Lattice, sales@fernlatticerentals.com, fernlatticerentals.com, 360-555-0182

Requirements
Must have
• Easy to read font
Should not have
• Orange anywhere in the design

```html
<!DOCTYPE html>
<html lang="en">
<head>
<meta charset="utf-8">
<title>Fern Lattice Table &amp; Chair Rentals – Business Card</title>
<link rel="stylesheet" href="https://fonts.googleapis.com/css2?family=Arimo:wght@400;700&family=Varela+Round&display=swap">
<style>
  :root {
    --page: #e9e7e3;
    --card: #ffffff;
    --ink: #2f3a38;
    --ink-soft: #4f5a58;
    --muted: #7d8786;
    --accent-green: #3f8f6b;
    --accent-blue: #2f6f9a;
    --shadow: rgba(0,0,0,0.18);
  }
  * { box-sizing: border-box; margin: 0; padding: 0; }
  html, body { width: 1200px; height: 892px; overflow: hidden; }
  body {
    background: var(--page);
    display: flex;
    align-items: center;
    justify-content: center;
    gap: 48px;
    font-family: "Arimo", Arial, sans-serif;
    color: var(--ink);
  }
  .card {
    width: 525px;
    height: 300px;
    background: var(--card);
    box-shadow: 0 6px 22px var(--shadow);
    position: relative;
  }

  /* Front */
  .card--front {
    padding: 96px 0 0 44px;
  }
  .card--front .brand-name {
    font-family: "Arimo", Arial, sans-serif;
    font-weight: 400;
    font-size: 52px;
    line-height: 1;
    color: var(--ink);
    letter-spacing: -0.5px;
  }
  .card--front .brand-tagline {
    font-family: "Varela Round", Arial, sans-serif;
    font-size: 27px;
    color: var(--ink-soft);
    margin-top: 16px;
    letter-spacing: 0.3px;
  }

  /* Back */
  .card--back .header {
    position: absolute;
    left: 36px;
    top: 26px;
  }
  .card--back .brand-name {
    font-weight: 400;
    font-size: 40px;
    line-height: 1;
    color: var(--ink);
  }
  .card--back .brand-tagline {
    font-size: 19px;
    color: var(--ink-soft);
    margin-top: 8px;
  }
  .card--back .rule {
    position: absolute;
    left: 0;
    right: 0;
    top: 120px;
    height: 2px;
    background: linear-gradient(90deg, var(--accent-green), var(--accent-blue));
  }
  .card--back .company {
    position: absolute;
    left: 36px;
    top: 140px;
    font-size: 22px;
    color: var(--ink-soft);
  }
  .card--back .contact-list {
    position: absolute;
    left: 36px;
    top: 184px;
    list-style: none;
    font-size: 14px;
    color: var(--muted);
    line-height: 22px;
  }
  .card--back .contact-list li {
    display: flex;
    align-items: center;
    gap: 8px;
  }
  .card--back .contact-list svg {
    width: 11px;
    height: 11px;
    flex: none;
  }
  .icon-fill { fill: var(--accent-green); }
  .icon-line { fill: none; stroke: var(--accent-green); }
  .card--back .hours {
    position: absolute;
    right: 30px;
    top: 190px;
    text-align: left;
    font-size: 15px;
    line-height: 20px;
    color: var(--ink-soft);
  }
</style>
</head>
<body>

  <section class="card card--front" aria-label="Card front">
    <h1 class="brand-name">Fern Lattice</h1>
    <p class="brand-tagline">Table and Chair Rentals</p>
  </section>

  <section class="card card--back" aria-label="Card back">
    <div class="header">
      <h2 class="brand-name">Fern Lattice</h2>
      <p class="brand-tagline">Table and Chair Rentals</p>
    </div>
    <div class="rule"></div>
    <p class="company">Fernlattice Event Rentals, LLC</p>
    <ul class="contact-list">
      <li>
        <svg viewBox="0 0 12 12" aria-hidden="true"><path class="icon-fill" d="M2.5 1 L4.5 1 L5.2 3.6 L4 4.6 C4.7 6 6 7.3 7.4 8 L8.4 6.8 L11 7.5 L11 9.5 C11 10.3 10.3 11 9.5 11 C5 11 1 7 1 2.5 C1 1.7 1.7 1 2.5 1 Z"/></svg>
        360-555-0182
      </li>
      <li>
        <svg viewBox="0 0 12 12" aria-hidden="true"><circle class="icon-line" cx="6" cy="6" r="5" stroke-width="1.4"/><path class="icon-line" d="M1 6 H11 M6 1 C3.5 3.5 3.5 8.5 6 11 M6 1 C8.5 3.5 8.5 8.5 6 11" stroke-width="1"/></svg>
        www.fernlatticerentals.com
      </li>
      <li>
        <svg viewBox="0 0 12 12" aria-hidden="true"><path class="icon-line" d="M1 2.5 H11 V9.5 H1 Z M1.5 3 L6 6.5 L10.5 3" stroke-width="1.3"/></svg>
        sales@fernlatticerentals.com
      </li>
    </ul>
    <div class="hours">
      <p>Mon-Fri: 8am to 6pm</p>
      <p>Saturday: 8am to 4pm</p>
      <p>Sunday: 9am to 1pm</p>
    </div>
  </section>

</body>
</html>
```